Shieldline Legal

I'm virtually ready to launch my site, but I have a number of edits and modifications that need to be implemented. More importantly, I'm always looking to improve my site, particularly now that I am making my proverbial "FIRST IMPRESSION." Thus, I'm willing to see if there is someone who can add creativity and perhaps improve what I already have, particularly on the All Important Front Page.

```html
<!DOCTYPE html>
<html lang="en">
<head>
<meta charset="utf-8">
<title>Shieldline Legal – Strength in Legal Protection</title>
<link href="https://fonts.googleapis.com/css2?family=Fira+Sans:wght@400;500;600&family=Lato:wght@400;700&display=swap" rel="stylesheet">
<style>
:root{
  --navy:#142a55;
  --navy-dark:#1b2140;
  --footer:#1c2242;
  --red:#b3141e;
  --red-soft:#c0454c;
  --ink:#1d2a4a;
  --muted:#8a8f9c;
  --line:#d9dce3;
  --light:#f3f4f7;
  --white:#ffffff;
  --field:#e4f1f8;
}
*{box-sizing:border-box;margin:0;padding:0}
html,body{width:1200px;height:5220px;overflow:hidden}
body{font-family:"Lato",sans-serif;color:var(--ink);background:var(--white);position:relative}
.abs{position:absolute}
h1,h2,h3,h4{font-family:"Fira Sans",sans-serif;font-weight:600}
.muted{color:var(--muted);font-size:13px;line-height:25px}
.eyebrow{font-family:"Fira Sans",sans-serif;font-size:11px;font-weight:600;color:var(--red);letter-spacing:.5px;text-transform:uppercase}
.eyebrow .dash{display:inline-block;width:10px;height:2px;background:var(--red);vertical-align:middle;margin:0 6px}
.center{text-align:center;left:0;width:1200px}

/* header */
.header{top:0;left:0;width:1200px;height:126px;background:var(--white)}
.contact-chip{display:flex;align-items:center;gap:10px;font-size:11px;line-height:13px}
.contact-chip .dot{width:30px;height:30px;border-radius:50%;background:var(--navy);display:flex;align-items:center;justify-content:center}
.contact-chip small{display:block;color:var(--muted);font-size:9px}
.brand{left:540px;top:22px;width:120px;text-align:center}
.brand .mark{width:70px;height:70px;border-radius:50%;background:var(--navy);margin:0 auto}
.brand span{display:block;font-family:"Fira Sans",sans-serif;font-size:11px;font-weight:600;color:var(--navy);margin-top:4px}
.btn-book{left:880px;top:14px;width:184px;height:40px;border-radius:20px;background:var(--navy);color:#fff;font-size:12px;font-weight:700;display:flex;align-items:center;justify-content:center}
.nav a{position:absolute;top:90px;font-size:12px;color:var(--ink);text-decoration:none}
.nav-rule{top:70px;left:700px;width:365px;height:1px;background:var(--line)}

/* hero */
.hero{top:126px;left:0;width:1200px;height:762px;background:linear-gradient(100deg,#2f3338 0%,#50565d 45%,#7d838a 75%,#6a7077 100%)}
.hero-kicker{left:80px;top:364px;color:#fff;font-family:"Fira Sans",sans-serif;font-size:24px;letter-spacing:3px}
.hero-title{left:78px;top:412px;color:#fff;font-size:50px;font-weight:600}
.hero-rule{left:80px;top:496px;width:725px;height:1px;background:rgba(255,255,255,.5)}
.hero-copy{left:82px;top:530px;width:640px;color:#fff;font-size:15px;font-weight:700;line-height:25px}
.btn{height:40px;border-radius:20px;font-size:14px;font-weight:700;display:flex;align-items:center;justify-content:center}
.btn-red{background:var(--red);color:#fff}
.btn-white{background:#fff;color:var(--ink)}

/* features */
.feature{width:320px;height:284px;background:#fff;border-radius:6px;box-shadow:0 6px 20px rgba(20,30,60,.12);text-align:center;padding-top:34px}
.feature .ico{width:56px;height:56px;margin:0 auto 20px;position:relative}
.feature .ico .blob{position:absolute;left:0;top:0;width:40px;height:40px;border-radius:50%;background:#f4d6d8}
.feature .ico svg{position:absolute;left:12px;top:10px}
.feature h3{color:var(--navy);font-size:18px;font-weight:500;margin-bottom:12px}
.feature p{padding:0 44px}

/* about */
.about-title{left:101px;top:1198px;font-size:35px;line-height:52px;color:var(--navy);width:460px}
.about-copy{left:101px;top:1316px;width:420px;font-size:12.5px;line-height:25px}
.btn-contact{left:101px;top:1548px;width:154px;height:44px;border-radius:3px;background:var(--red-soft);color:#fff;font-size:15px;font-weight:700;display:flex;align-items:center;justify-content:center;gap:14px}
.about-photo{left:608px;top:1186px;width:497px;height:405px;border-radius:4px;background:linear-gradient(110deg,#3b4148,#8a9096 45%,#c9ccd0 80%,#9aa0a6)}
.orbit{left:534px;top:1290px;width:160px;height:160px;border-radius:50%;border:2px dashed #c9ccd3;clip-path:inset(0 50% 0 0)}
.orbit-dot{left:590px;top:1346px;width:50px;height:50px;border-radius:50%;background:#fff;box-shadow:0 2px 10px rgba(0,0,0,.2);display:flex;align-items:center;justify-content:center}
.orbit-dot i{width:28px;height:28px;border-radius:50%;background:var(--navy);display:block}

/* services */
.services{top:1666px;left:0;width:1200px;height:655px;background:var(--light)}
.sec-title{font-size:34px;color:var(--navy)}
.svc{width:320px;height:286px;top:1928px}
.svc .img{width:100%;height:100%;border-radius:6px}
.svc .label{position:absolute;left:58px;bottom:-28px;width:204px;height:50px;background:#fff;border-radius:4px;box-shadow:0 4px 14px rgba(0,0,0,.12);font-family:"Fira Sans",sans-serif;font-weight:600;font-size:19px;color:var(--navy);display:flex;align-items:center;justify-content:center}

/* call band */
.callband{top:2321px;left:0;width:1200px;height:308px;background:linear-gradient(90deg,#3a3d42,#5a5e63 50%,#45484d)}
.call-title{top:2430px;font-family:"Fira Sans",sans-serif;font-size:35px;color:#fff;line-height:42px;font-weight:500}
.call-title em{color:var(--red);font-style:normal}
.call-bar{left:351px;top:2598px;width:500px;height:54px;background:#fff;border-radius:3px;box-shadow:0 4px 14px rgba(0,0,0,.15);display:flex;align-items:center;justify-content:space-around;font-size:16px;padding:0 20px}

/* reviews */
.review{width:324px;height:324px;top:2895px;background:#fff;box-shadow:0 4px 16px rgba(20,30,60,.1);text-align:center;padding-top:68px}
.review .stars{color:#ef7c1a;font-size:20px;letter-spacing:8px;margin-bottom:14px}
.review p{padding:0 56px}
.avatar{width:70px;height:70px;border-radius:50%;top:2863px}
.quote{width:72px;height:36px;border-radius:36px 36px 0 0;background:var(--navy);top:3130px;display:flex;align-items:flex-end;justify-content:center;color:#fff;font-family:"Fira Sans",sans-serif;font-size:30px;font-weight:600;line-height:30px}
.rname{top:3198px;width:324px;text-align:center;font-family:"Fira Sans",sans-serif;font-weight:500;font-size:17px;color:#555b68}
.rloc{top:3228px;width:324px;text-align:center;font-size:12px;color:var(--muted)}

/* excellence */
.excel{top:3298px;left:0;width:1200px;height:604px;background:linear-gradient(100deg,#1f2e3c,#3a5060 45%,#6d7e88 70%,#2c3a47)}
.excel-card{left:91px;top:3365px;width:494px;height:466px;background:#fff;border-radius:8px;padding:56px 52px}
.excel-card h2{font-size:34px;color:var(--navy);margin:12px 0 28px}
.point{display:flex;gap:26px;margin-bottom:22px}
.point h4{font-size:12px;color:var(--navy);font-weight:600;margin-bottom:2px}
.point p{font-size:12px;line-height:25px}

/* form */
.form-card{left:140px;top:4119px;width:912px;height:478px;background:#fff;border-radius:10px;box-shadow:0 4px 24px rgba(20,30,60,.1)}
.field{position:absolute;height:42px;border:1.5px solid var(--navy);border-radius:21px;padding:14px 34px 0}
.field.active{background:var(--field)}
.field label{position:absolute;top:-9px;left:30px;background:#fff;padding:0 6px;font-size:12px;color:var(--ink)}
.field.active label{background:linear-gradient(#fff 50%,var(--field) 50%)}
.field span{font-size:12px;color:var(--muted);font-style:italic}
.area{border-radius:18px;height:150px}
.socials-sm{position:absolute;left:66px;top:410px;display:flex;gap:10px}
.socials-sm i{width:30px;height:30px;border-radius:50%;border:1.5px solid #6b8cc4;display:block}
.btn-submit{position:absolute;left:704px;top:402px;width:142px;height:40px;border-radius:20px;background:var(--red);color:#fff;font-size:12px;font-weight:700;display:flex;align-items:center;justify-content:center;gap:14px}
.btn-submit b{width:24px;height:24px;border-radius:50%;background:#fff;display:block}

/* footer */
.footer{top:4664px;left:0;width:1200px;height:495px;background:var(--footer)}
.fsoc{top:4764px;width:38px;height:38px;border-radius:3px;background:#3a5ea8}
.foot-brand{left:540px;top:4710px;width:120px;text-align:center}
.foot-brand .mark{width:90px;height:90px;border-radius:50%;background:#2b335a;margin:0 auto}
.foot-brand span{display:block;color:#fff;font-family:"Fira Sans",sans-serif;font-size:12px;font-weight:600;margin-top:6px}
.totop{left:972px;top:4764px;display:flex;align-items:center;gap:16px;color:#fff;font-size:14px;font-weight:700}
.totop i{width:44px;height:44px;background:var(--red);border-radius:3px;display:flex;align-items:center;justify-content:center}
.foot-rule{left:84px;top:4838px;width:1032px;height:1px;background:rgba(255,255,255,.35)}
.foot-title{top:4900px;color:#fff;font-size:28px}
.foot-copy{top:4950px;color:#fff;font-size:15px;line-height:26px}
.fcontact{top:5044px;display:flex;align-items:center;gap:14px;color:#fff;font-size:14px;line-height:20px}
.fcontact b{display:block;font-size:15px}
.fsep{top:5040px;width:1px;height:60px;background:rgba(255,255,255,.4)}
.bottom{top:5159px;left:0;width:1200px;height:61px;background:#252b4d;color:#fff;font-size:12px;font-weight:700}
</style>
</head>
<body>

<!-- Header -->
<header class="header abs">
  <div class="contact-chip abs" style="left:122px;top:22px">
    <span class="dot"><svg width="14" height="14" viewBox="0 0 24 24"><path d="M6 3l3 5-2 2a12 12 0 0 0 7 7l2-2 5 3-2 4C11 22 2 13 2 5z" fill="#fff"/></svg></span>
    <div>Call Us:<small>0212 555 0142</small></div>
  </div>
  <div class="contact-chip abs" style="left:282px;top:22px">
    <span class="dot"><svg width="14" height="12" viewBox="0 0 24 18"><rect x="1" y="1" width="22" height="16" rx="2" fill="#fff"/><path d="M2 2l10 8 10-8" stroke="#142a55" stroke-width="2" fill="none"/></svg></span>
    <div>Email:<small>office@shieldline.example</small></div>
  </div>
  <div class="brand abs"><div class="mark"></div><span>Shieldline Legal</span></div>
  <div class="btn-book abs">BOOK APPOINTMENT</div>
  <div class="nav-rule abs"></div>
  <nav class="nav">
    <a style="left:124px">Home</a><a style="left:236px">About Us</a><a style="left:386px">Services</a>
    <a style="left:704px">Team</a><a style="left:832px">Blog</a><a style="left:958px">Contact Us</a>
  </nav>
</header>

<!-- Hero -->
<section class="hero abs" role="img" aria-label="Lawyers working together in a bright office"></section>
<div class="hero-kicker abs">LEGAL SERVICES</div>
<h1 class="hero-title abs">Strength in Legal Protection</h1>
<div class="hero-rule abs"></div>
<p class="hero-copy abs">Lorem ipsum dolor sit amet, consectetur adipiscing elit et dolore conser tempor incididunt ut labore et dolore magna</p>
<div class="btn btn-red abs" style="left:84px;top:614px;width:146px">LEARN MORE</div>
<div class="btn btn-white abs" style="left:240px;top:614px;width:180px">REQUEST QUOTE</div>

<!-- Features -->
<div class="feature abs" style="left:91px;top:805px">
  <div class="ico"><span class="blob"></span><svg width="36" height="36" viewBox="0 0 36 36" fill="none" stroke="#b3141e" stroke-width="2"><path d="M6 30h24M12 24l10-14M18 8l8 6M10 28l4-4"/></svg></div>
  <h3>Professionalism</h3><p class="muted">Lorem ipsum dolor sit amet, consect adipiscing elit, sed do eiusmod tempor incididunt ut labore et dolore</p>
</div>
<div class="feature abs" style="left:442px;top:805px">
  <div class="ico"><span class="blob"></span><svg width="36" height="36" viewBox="0 0 36 36" fill="none" stroke="#b3141e" stroke-width="2"><path d="M5 26a13 13 0 1 1 26 0"/><path d="M18 26l6-9"/><circle cx="18" cy="26" r="2"/></svg></div>
  <h3>Affordable</h3><p class="muted">Lorem ipsum dolor sit amet, consect adipiscing elit, sed do eiusmod tempor incididunt ut labore et dolore</p>
</div>
<div class="feature abs" style="left:786px;top:805px">
  <div class="ico"><span class="blob"></span><svg width="36" height="36" viewBox="0 0 36 36" fill="none" stroke="#b3141e" stroke-width="2"><path d="M18 4l4 9 10 1-7 7 2 10-9-5-9 5 2-10-7-7 10-1z"/></svg></div>
  <h3>Legal Experts</h3><p class="muted">Lorem ipsum dolor sit amet, consect adipiscing elit, sed do eiusmod tempor incididunt ut labore et dolore</p>
</div>

<!-- About -->
<div class="eyebrow abs" style="left:101px;top:1180px">See the difference<span class="dash"></span></div>
<h2 class="about-title abs">Turning Challenges into Legal Triumphs</h2>
<p class="about-copy muted abs">Lorem ipsum dolor sit amet, consectetur adipiscing elit, sed do eius od tempor incididunt ut labore et dolore magna aliqua. Ut enim ad minim veniam, quis nostrud exercitation ullamco laboris nisi ut ali quip ex ea commodo consequat. Duis aute irure dolor in re prehenderit in voluptate velit esse cillum dolore eu fugiat nulla pariatur. Excepteur sint occaecat cupidatat non proident, sunt in culpa qui officia deserunt mollit anim id est laborum pariatur. Exce pteur sint occaecat cupidatat non proident, sunt in culpa qui</p>
<div class="btn-contact abs">Contact us <svg width="18" height="14" viewBox="0 0 18 14" fill="none" stroke="#fff" stroke-width="2"><path d="M1 7h15M10 1l6 6-6 6"/></svg></div>
<div class="orbit abs"></div>
<div class="about-photo abs" role="img" aria-label="Two lawyers shaking hands in an office"></div>
<div class="orbit-dot abs"><i></i></div>

<!-- Services -->
<section class="services abs"></section>
<div class="eyebrow abs center" style="top:1746px"><span class="dash"></span>Our services<span class="dash"></span></div>
<h2 class="sec-title abs center" style="top:1768px">Services We Offer</h2>
<p class="muted abs" style="left:300px;top:1834px;width:600px;text-align:center">Lorem ipsum dolor sit amet, consectetur adipiscing elit, sed do eiusod tempor incididunt ut la bore et dolore magna aliqua. Ut enim ad minim veniam, quis nostrud exercitation</p>
<div class="svc abs" style="left:93px"><div class="img" role="img" aria-label="Hand touching legal icons on a blue screen" style="background:linear-gradient(135deg,#1f3f6e,#4d86b8 55%,#a9c9e2)"></div><div class="label">Consultation</div></div>
<div class="svc abs" style="left:442px"><div class="img" role="img" aria-label="Judge holding a wooden gavel" style="background:linear-gradient(135deg,#6b5a48,#2e2621 55%,#8b6a48)"></div><div class="label">Litigation</div></div>
<div class="svc abs" style="left:788px"><div class="img" role="img" aria-label="Scales of justice and gavel on a desk with documents" style="background:linear-gradient(135deg,#5d5f5f,#9a9c9a 55%,#d3d3cf)"></div><div class="label">Collection Claims</div></div>

<!-- Call band -->
<section class="callband abs" role="img" aria-label="Team of people in a meeting, darkened"></section>
<h2 class="call-title abs center">We're on Call <em>24/7</em> t React Promptly to Your<br>Legal Services</h2>
<div class="call-bar abs"><span>+ (001) 234-567-890</span><span>[or]</span><span>info@example.com</span></div>

<!-- Reviews -->
<div class="eyebrow abs center" style="top:2690px"><span class="dash"></span>Testimonials<span class="dash"></span></div>
<h2 class="sec-title abs center" style="top:2710px">Client Reviews</h2>
<p class="muted abs" style="left:300px;top:2774px;width:600px;text-align:center">Lorem ipsum dolor sit amet, consectetur adipiscing elit, sed do eiusod tempor incididunt ut la bore et dolore magna aliqua. Ut enim ad minim veniam, quis nostrud exercitation</p>

<div class="review abs" style="left:91px"><div class="stars">★★★★★</div><p class="muted">Lorem ipsum dolor sit amet, consectetur adipiscing elit, sed do eiusmod tempor incididunt ut labore et dolore</p></div>
<div class="review abs" style="left:442px"><div class="stars">★★★★★</div><p class="muted">Lorem ipsum dolor sit amet, consectetur adipiscing elit, sed do eiusmod tempor incididunt ut labore et dolore</p></div>
<div class="review abs" style="left:793px"><div class="stars">★★★★★</div><p class="muted">Lorem ipsum dolor sit amet, consectetur adipiscing elit, sed do eiusmod tempor incididunt ut labore et dolore</p></div>
<div class="avatar abs" role="img" aria-label="Client portrait" style="left:218px;background:linear-gradient(#e9c9a4,#3c6fa8)"></div>
<div class="avatar abs" role="img" aria-label="Client portrait" style="left:569px;background:linear-gradient(#f3b9b9,#e58b8b)"></div>
<div class="avatar abs" role="img" aria-label="Client portrait" style="left:920px;background:linear-gradient(#f1f1f1,#d8d8d8)"></div>
<div class="quote abs" style="left:217px">❝</div>
<div class="quote abs" style="left:568px">❝</div>
<div class="quote abs" style="left:919px">❝</div>
<div class="rname abs" style="left:91px">Grant Lester</div><div class="rloc abs" style="left:91px">Los Angeles</div>
<div class="rname abs" style="left:442px">Grant Lester</div><div class="rloc abs" style="left:442px">Los Angeles</div>
<div class="rname abs" style="left:793px">Grant Lester</div><div class="rloc abs" style="left:793px">Los Angeles</div>

<!-- Excellence -->
<section class="excel abs" role="img" aria-label="Business people in a glass-walled meeting room"></section>
<div class="excel-card abs">
  <div class="eyebrow">See the difference<span class="dash"></span></div>
  <h2>Legal Excellence</h2>
  <div class="point"><svg width="30" height="30" viewBox="0 0 36 36" fill="none" stroke="#b3141e" stroke-width="2"><path d="M6 30h24M12 24l10-14M18 8l8 6M10 28l4-4"/></svg><div><h4>Client Centric</h4><p class="muted">Lorem ipsum dolor sit amet, consectetur adipiscing elit, od tempor incididunt ut labore et dolore magna</p></div></div>
  <div class="point"><svg width="30" height="30" viewBox="0 0 36 36" fill="none" stroke="#b3141e" stroke-width="2"><path d="M18 4l4 9 10 1-7 7 2 10-9-5-9 5 2-10-7-7 10-1z"/></svg><div><h4>Free Consultation</h4><p class="muted">Lorem ipsum dolor sit amet, consectetur adipiscing elit, od tempor incididunt ut labore et dolore magna</p></div></div>
  <div class="point"><svg width="30" height="30" viewBox="0 0 36 36" fill="none" stroke="#b3141e" stroke-width="2"><path d="M5 26a13 13 0 1 1 26 0"/><path d="M18 26l6-9"/></svg><div><h4>Minimize Exposure</h4><p class="muted">Lorem ipsum dolor sit amet, consectetur adipiscing elit, od tempor incididunt ut labore et dolore magna</p></div></div>
</div>

<!-- Contact -->
<div class="eyebrow abs center" style="top:3954px"><span class="dash"></span>Contact us<span class="dash"></span></div>
<h2 class="sec-title abs center" style="top:3974px">Get in touch with us</h2>
<p class="muted abs" style="left:300px;top:4038px;width:600px;text-align:center">Lorem ipsum dolor sit amet, consectetur adipiscing elit, sed do eiusod tempor incididunt ut la bore et dolore magna aliqua. Ut enim ad minim veniam, quis nostrud exercitation</p>
<form class="form-card abs">
  <div class="field active" style="left:54px;top:60px;width:392px"><label>Your Name</label><span>Type Name</span></div>
  <div class="field" style="left:466px;top:60px;width:392px"><label>Your Website</label><span>www.company.com</span></div>
  <div class="field" style="left:54px;top:134px;width:392px"><label>Your Phone</label><span>123 456 789</span></div>
  <div class="field" style="left:466px;top:134px;width:392px"><label>Your Email</label><span>info@company.com</span></div>
  <div class="field area" style="left:54px;top:210px;width:804px"><label>Your Message</label><span>Type Message</span></div>
  <div class="socials-sm"><i></i><i></i><i></i><i></i></div>
  <div class="btn-submit">Submit Now <b></b></div>
</form>

<!-- Footer -->
<footer class="footer abs"></footer>
<div class="fsoc abs" style="left:86px"></div>
<div class="fsoc abs" style="left:136px;background:#2f5a9e"></div>
<div class="fsoc abs" style="left:186px;background:#2a8fd0"></div>
<div class="fsoc abs" style="left:236px;background:#d9232a"></div>
<div class="foot-brand abs"><div class="mark"></div><span>Shieldline Legal</span></div>
<div class="totop abs">Back to top <i><svg width="18" height="12" viewBox="0 0 18 12" fill="none" stroke="#fff" stroke-width="2.5"><path d="M2 10l7-7 7 7"/></svg></i></div>
<div class="foot-rule abs"></div>
<h2 class="foot-title abs center">Get free assessment today</h2>
<p class="foot-copy abs" style="left:300px;width:600px;text-align:center">Lorem ipsum dolor sit amet, consectetur adipiscing elit, sed do eiusod tempor incididunt ut labore et dolore magna aliqua.</p>
<div class="fcontact abs" style="left:234px"><svg width="34" height="44" viewBox="0 0 34 44" fill="none" stroke="#b3141e" stroke-width="2"><rect x="6" y="2" width="22" height="40" rx="3"/><path d="M14 36h6"/></svg><div>Make a Call<b>+1-234-567-8910</b></div></div>
<div class="fsep abs" style="left:454px"></div>
<div class="fcontact abs" style="left:478px"><svg width="44" height="44" viewBox="0 0 44 44" fill="none" stroke="#b3141e" stroke-width="2"><rect x="2" y="10" width="40" height="28" rx="2"/><path d="M2 12l20 14 20-14"/></svg><div>Mail Us On<b>info@company.com</b></div></div>
<div class="fsep abs" style="left:728px"></div>
<div class="fcontact abs" style="left:758px"><svg width="44" height="44" viewBox="0 0 44 44" fill="none" stroke="#b3141e" stroke-width="2"><path d="M22 38S10 24 10 16a12 12 0 0 1 24 0c0 8-12 22-12 22z"/><circle cx="22" cy="16" r="4"/><path d="M4 42h36"/></svg><div>Location<b>256 Area Place Rd</b></div></div>
<div class="bottom abs">
  <span class="abs" style="left:86px;top:22px">SHIELDLINE LEGAL</span>
  <span class="abs" style="left:802px;top:22px">Privacy Policy</span>
  <span class="abs" style="left:916px;top:22px">Terms &amp; Conditions</span>
  <span class="abs" style="left:1056px;top:22px">Site Map</span>
</div>

</body>
</html>
```